Web Design Project

We are looking to for a redesign for www.volketa.com. Volketa Systems is a Managed Service Provider of IT solutions based is Calgary, Alberta, Canada. We are currently expanding into the Edmonton market and would like to lauch our new site with our expansion.
The design should be sleak in style and communicate a professional vision to our clients and prospects.

Thanks,
Dale

Target Market(s)

Small to medium size businesses looking to outsource or complement their IT solutions.

Industry/Entity Type

It Professional

```html
<!DOCTYPE html>
<html lang="en">
<head>
<meta charset="utf-8">
<title>Volketa Systems – Managed IT Services</title>
<link href="https://fonts.googleapis.com/css2?family=Michroma&family=Ubuntu:wght@400;500&family=Lato:ital,wght@0,400;0,700;1,400&display=swap" rel="stylesheet">
<style>
:root{
  --red:#c8070f;
  --red-dark:#a9050c;
  --ink:#2a2a2a;
  --text:#555;
  --line:#d8d8d8;
  --footer:#f2f2f2;
  --sky-top:#cfe6f5;
  --white:#fff;
}
*{box-sizing:border-box;margin:0;padding:0}
html,body{width:846px;height:1200px;overflow:hidden}
body{position:relative;background:var(--white);font-family:"Lato",sans-serif;color:var(--text)}
.abs{position:absolute}
.header{left:0;top:0;width:846px;height:150px;background:linear-gradient(180deg,var(--sky-top) 0%,#eef6fb 55%,#fff 100%);border-top:3px solid #1a1a1a}
.brand-name{left:24px;top:42px;font-family:"Ubuntu",sans-serif;font-weight:500;font-size:28px;color:var(--ink);line-height:1}
.search{left:599px;top:14px;width:215px;height:26px;background:#fff;border:1px solid #d4dde3;font-size:10px;color:#777;padding:7px 8px}
.search svg{position:absolute;right:7px;top:5px}
.support-icon{left:607px;top:44px;width:50px;height:50px;border-radius:6px;background:linear-gradient(180deg,#e6e6e6,#9a9a9a)}
.support-label{left:667px;top:63px;font-family:"Michroma",sans-serif;font-size:11px;color:#4a4a4a;letter-spacing:1px}
.nav{left:34px;top:97px;width:780px;height:43px;background:var(--red);display:flex;list-style:none}
.nav li{font-family:"Ubuntu",sans-serif;font-size:13px;color:#fff;line-height:43px;padding-left:23px;border-right:1px solid var(--red-dark)}
.nav li:nth-child(1){width:84px;padding-left:33px}
.nav li:nth-child(2){width:88px}
.nav li:nth-child(3){width:93px}
.nav li:nth-child(4){width:83px}
.nav li:last-child{border-right:none;padding-left:22px}
.hero{left:34px;top:150px;width:780px;height:318px;background:linear-gradient(180deg,#fff 0%,#e2e2e2 100%)}
.hero-photo{left:20px;top:21px;width:421px;height:278px;background:#fff;padding:4px;box-shadow:0 10px 8px -8px rgba(0,0,0,.45)}
.hero-photo div{width:100%;height:100%;background:linear-gradient(135deg,#f0f0f0 0%,#8f8f8f 45%,#3d4450 75%,#e7e7e7 100%)}
.hero-title{left:457px;top:52px;width:310px;font-family:"Michroma",sans-serif;font-weight:400;font-size:15.5px;line-height:29px;color:var(--red);letter-spacing:.5px}
.hero-text{left:457px;top:131px;width:305px;font-size:10.2px;line-height:20px;color:#444}
.btn-more{left:646px;top:240px;width:101px;height:26px;background:linear-gradient(#fff,#ececec);box-shadow:0 1px 2px rgba(0,0,0,.15);font-family:"Ubuntu",sans-serif;font-weight:500;font-size:11px;color:var(--red);text-align:center;line-height:26px}
.dots{left:471px;top:287px;display:flex;gap:4px}
.dots span{width:9px;height:9px;border-radius:50%;background:#111}
.dots span.on{background:var(--red)}
.feature{top:512px}
.feature h3{font-family:"Michroma",sans-serif;font-weight:400;font-size:11.5px;color:#333;letter-spacing:1px;margin-bottom:11px}
.feature p{font-size:9px;line-height:15px;color:#555}
.feature a{display:block;margin-top:12px;font-size:9px;color:var(--red);text-decoration:none;padding-left:2px}
.feature-icon{top:522px}
.welcome-title{left:48px;top:657px;font-family:"Michroma",sans-serif;font-weight:400;font-size:14px;color:#333;letter-spacing:1.5px}
.welcome-text{left:50px;top:693px;width:492px;font-size:9px;line-height:15.7px;color:#444}
.welcome-text p+p{margin-top:15.7px}
.team-photo{left:557px;top:682px;width:261px;height:134px;background:linear-gradient(180deg,#f4f4f4 0%,#d9dde2 70%,#bfc6cc 100%)}
.partners{left:4px;top:841px;width:833px;height:142px;background:#f6f6f6}
.partners h3{position:absolute;left:50px;top:20px;font-family:"Michroma",sans-serif;font-weight:400;font-size:11px;color:#444;letter-spacing:1px}
.badge{top:51px;width:82px;height:64px;background:#e0e0e0;border-radius:4px}
.badge.blue{background:#1e63b8;border-radius:0}
.footer{left:0;top:983px;width:846px;height:178px;background:var(--footer)}
.signup h3,.fcol h3{font-family:"Ubuntu",sans-serif;font-weight:400;font-size:13px;color:#222}
.signup{left:42px;top:32px;width:230px}
.signup p{margin-top:9px;font-size:8.5px;line-height:14px;color:#333}
.email{left:0;top:62px;width:224px;height:22px;background:#fff;font-style:italic;font-size:8.5px;color:#999;padding:6px 9px;box-shadow:0 5px 5px -4px rgba(0,0,0,.25)}
.subscribe{left:148px;top:90px;width:72px;height:24px;background:var(--red);border:1px solid #e55;border-radius:3px;color:#fff;font-family:"Ubuntu",sans-serif;font-weight:500;font-size:10.5px;text-align:center;line-height:22px}
.divider{left:297px;top:19px;width:1px;height:158px;background:var(--line)}
.fcol{top:36px;width:140px}
.fcol ul{list-style:none;margin-top:14px}
.fcol li{font-size:9px;color:#555;line-height:20px}
.copyright{left:40px;top:1177px;font-size:9px;color:#444}
</style>
</head>
<body>

<header class="abs header">
  <div class="abs brand-name">Volketa Systems</div>
  <div class="abs search">enter keyword
    <svg width="15" height="15" viewBox="0 0 15 15"><circle cx="6" cy="6" r="4.5" fill="none" stroke="#666" stroke-width="2"/><line x1="9.5" y1="9.5" x2="13.5" y2="13.5" stroke="#666" stroke-width="2.4" stroke-linecap="round"/></svg>
  </div>
  <div class="abs support-icon" role="img" aria-label="Support agent with headset at a laptop"></div>
  <div class="abs support-label">LIVE SUPPORT</div>
</header>

<ul class="abs nav">
  <li>Home</li><li>About Us</li><li>Solutions</li><li>Services</li><li>Contact Us</li>
</ul>

<section class="abs hero">
  <div class="abs hero-photo"><div role="img" aria-label="Business team reviewing work on a laptop"></div></div>
  <h1 class="abs hero-title">MANAGED IT SERVICE PROFESSIONALS</h1>
  <p class="abs hero-text">Volketa Systems employs an innovative managed service solution to provide our clients with technical expertise and superb customer service. Our goal is to ensure that our clients business requirements align with their technical needs in order to maximize their benefits</p>
  <div class="abs btn-more">LEARN MORE</div>
  <div class="abs dots"><span></span><span></span><span class="on"></span></div>
</section>

<svg class="abs feature-icon" style="left:35px" width="36" height="54" viewBox="0 0 36 54"><path d="M18 2a15 15 0 0 0-9 27c2 2 3 4 3 7v4h12v-4c0-3 1-5 3-7A15 15 0 0 0 18 2z" fill="none" stroke="#b8b8b8" stroke-width="2"/><rect x="12" y="43" width="12" height="3" fill="#b8b8b8"/><rect x="12" y="48" width="12" height="3" fill="#b8b8b8"/><line x1="18" y1="16" x2="18" y2="38" stroke="#ccc" stroke-width="1.5"/></svg>
<div class="abs feature" style="left:80px;width:178px"><h3>DEVELOPMENT</h3><p>Enhance your footprint on the World Wide Web or have a custom application developed to improve your productivity.</p><a>View More</a></div>

<svg class="abs feature-icon" style="left:318px" width="42" height="52" viewBox="0 0 42 52"><circle cx="21" cy="20" r="18" fill="none" stroke="#b8b8b8" stroke-width="2"/><ellipse cx="21" cy="20" rx="8" ry="18" fill="none" stroke="#b8b8b8" stroke-width="1.6"/><line x1="3" y1="20" x2="39" y2="20" stroke="#b8b8b8" stroke-width="1.6"/><line x1="6" y1="11" x2="36" y2="11" stroke="#b8b8b8" stroke-width="1.4"/><line x1="6" y1="29" x2="36" y2="29" stroke="#b8b8b8" stroke-width="1.4"/><line x1="21" y1="38" x2="21" y2="46" stroke="#b8b8b8" stroke-width="2"/><line x1="4" y1="47" x2="38" y2="47" stroke="#b8b8b8" stroke-width="2"/><circle cx="21" cy="47" r="3" fill="#b8b8b8"/></svg>
<div class="abs feature" style="left:372px;top:516px;width:150px"><h3>MANAGEMENT</h3><p>The Manage Layer establishes an integrated approach to IT service management activities.</p><a>View More</a></div>

<svg class="abs feature-icon" style="left:578px" width="42" height="42" viewBox="0 0 42 42"><circle cx="21" cy="21" r="21" fill="#c4c4c4"/><g transform="rotate(-18 21 21)" fill="#fff"><rect x="11" y="12" width="20" height="4"/><rect x="11" y="19" width="20" height="4"/><rect x="11" y="26" width="20" height="4"/></g></svg>
<div class="abs feature" style="left:634px;top:516px;width:180px"><h3>STORAGE</h3><p>All Data Is Important! Make Sure You Have The Space To Handle Yours.</p><a style="margin-top:22px">View More</a></div>

<h2 class="abs welcome-title">WELCOME TO VSI</h2>
<div class="abs welcome-text">
  <p>After nearly a decade in the business, Halvorsen IT has found that simply providing our clients high-quality management of their desktops, servers, network and security is not enough. That's why we changed our business model to better meet specific client needs.</p>
  <p>We are cost-effective and quick to respond. We offer client-friendly fee structures and billing processes. We go above and beyond to develop long-term strategies that make technology work better for you now and in the future. In addition, our team members are friendly and approachable, contradicting the cold 'techno geek' stereotype.</p>
</div>
<div class="abs team-photo" role="img" aria-label="Business professionals standing on puzzle pieces"></div>

<section class="abs partners">
  <h3>PARTNERS</h3>
  <div class="abs badge" style="left:62px"></div>
  <div class="abs badge" style="left:198px"></div>
  <div class="abs badge" style="left:324px"></div>
  <div class="abs badge" style="left:449px"></div>
  <div class="abs badge blue" style="left:586px"></div>
  <div class="abs badge" style="left:721px"></div>
</section>

<footer class="abs footer">
  <div class="abs signup">
    <h3>Sign Up to Stay in Touch</h3>
    <p>Please enter your email address below to sign up<br>for our mailing list.</p>
    <div class="abs email">your email address here..</div>
    <div class="abs subscribe">Subscribe ›</div>
  </div>
  <div class="abs divider"></div>
  <div class="abs fcol" style="left:339px"><h3>About Us</h3><ul><li>Company</li><li>Mission</li><li>History</li><li>Community</li></ul></div>
  <div class="abs fcol" style="left:496px"><h3>Solutions</h3><ul><li>Managed Services</li><li>Virtualization</li><li>Online Backup</li><li>Development</li><li>Storage</li></ul></div>
  <div class="abs fcol" style="left:662px"><h3>Services</h3><ul><li>Planning</li><li>Delivery</li><li>Operation</li><li>Management</li><li>Careers</li></ul></div>
</footer>

<div class="abs copyright">© 2012 volketa &nbsp;|&nbsp; All right reserved</div>

</body>
</html>
```